Business Card for Coastal Tundrabridge Advisory

We need a business card for Coastal Tundrabridge Advisory. The company website address is provided below. The company logo is attached. We provide specialized permafrost services to the mining, transportation, and oil & gas industries. The card should be prepared for:
Matthias Korhonen, PhD.
Coastal Tundrabridge Advisory
PO Box 418259
Quillwater, Alaska 99642
Direct: +1-907-555-0143
Email: mkorhonen@tundrabridgeadvisory.example
Website: www.coastaltundrabridgeadvisory.example

```html
<!DOCTYPE html>
<html lang="en">
<head>
<meta charset="utf-8">
<title>Coastal Tundrabridge Advisory – Business Card</title>
<link rel="stylesheet" href="https://fonts.googleapis.com/css2?family=Roboto:wght@300;400;700&display=swap">
<style>
  :root {
    --backdrop: #232323;
    --card: #111722;
    --ink: #f2f4f7;
    --ink-soft: #d9dde3;
    --rule: #c9ced6;
  }
  * { box-sizing: border-box; margin: 0; padding: 0; }
  html, body {
    width: 1200px; height: 711px; overflow: hidden;
    background: var(--backdrop);
    font-family: "Roboto", Arial, sans-serif;
    color: var(--ink);
  }
  .sheet {
    position: relative; width: 1200px; height: 711px;
    display: flex; align-items: center; justify-content: center; gap: 40px;
  }
  .card {
    position: relative; width: 540px; height: 309px;
    background: var(--card);
    border-radius: 3px;
  }
  .wordmark {
    font-weight: 400; text-transform: uppercase; color: var(--ink);
    line-height: 1.25;
  }
  .card-front .wordmark {
    position: absolute; left: 0; right: 0; top: 50%;
    transform: translateY(-50%);
    text-align: center; font-size: 30px; letter-spacing: 3px;
  }
  .card-front .wordmark .line-small { display: block; font-size: 30px; letter-spacing: 12px; }
  .card-back .wordmark {
    position: absolute; left: 34px; top: 150px; width: 240px;
    font-size: 16px; letter-spacing: 1.5px;
  }
  .card-back .wordmark .line-small { display: block; letter-spacing: 6px; }
  .divider {
    position: absolute; left: 290px; top: 48px; width: 1px; height: 186px;
    background: var(--rule);
  }
  .identity { position: absolute; left: 308px; top: 52px; }
  .identity .person { font-size: 22px; line-height: 1.1; white-space: nowrap; }
  .identity .first { font-weight: 700; }
  .identity .last { font-weight: 300; }
  .identity .degree { font-size: 12px; font-weight: 700; margin-top: 2px; }
  .contacts { position: absolute; left: 308px; top: 138px; list-style: none; }
  .contacts li {
    display: flex; align-items: center; gap: 6px;
    font-size: 10.5px; font-weight: 400; color: var(--ink-soft);
    line-height: 18px; white-space: nowrap;
  }
  .contacts svg { width: 11px; height: 11px; flex: none; fill: var(--ink-soft); }
  .address {
    position: absolute; left: 0; right: 0; bottom: 26px;
    text-align: center; font-size: 12px; font-weight: 400; color: var(--ink-soft);
    padding-left: 150px;
  }
</style>
</head>
<body>
<main class="sheet">
  <section class="card card-front" aria-label="Card front">
    <div class="wordmark">Coastal Tundrabridge<span class="line-small">Advisory</span></div>
  </section>

  <section class="card card-back" aria-label="Card back">
    <div class="wordmark">Coastal Tundrabridge<span class="line-small">Advisory</span></div>
    <div class="divider"></div>
    <div class="identity">
      <p class="person"><span class="first">Matthias</span> <span class="last">Korhonen</span></p>
      <p class="degree">PhD</p>
    </div>
    <ul class="contacts">
      <li>
        <svg viewBox="0 0 24 24" aria-hidden="true"><path d="M6.6 10.8a15.1 15.1 0 0 0 6.6 6.6l2.2-2.2a1 1 0 0 1 1-.25 11.4 11.4 0 0 0 3.6.57 1 1 0 0 1 1 1V20a1 1 0 0 1-1 1A17 17 0 0 1 3 4a1 1 0 0 1 1-1h3.5a1 1 0 0 1 1 1c0 1.25.2 2.45.57 3.57a1 1 0 0 1-.25 1z"/></svg>
        +1-907-555-0143
      </li>
      <li>
        <svg viewBox="0 0 24 24" aria-hidden="true"><path d="M2 5h20v14H2zm2 2v.5l8 5 8-5V7zm0 2.8V17h16V9.8l-8 5z"/></svg>
        mkorhonen@tundrabridgeadvisory.example
      </li>
      <li>
        <svg viewBox="0 0 24 24" aria-hidden="true"><path d="M12 2a10 10 0 1 0 0 20 10 10 0 0 0 0-20zm6.9 6h-3a15.7 15.7 0 0 0-1.4-3.6A8 8 0 0 1 18.9 8zM12 4a14 14 0 0 1 1.9 4h-3.8A14 14 0 0 1 12 4zM4.3 14a8 8 0 0 1 0-4h3.4a16.5 16.5 0 0 0 0 4zm.8 2h3a15.7 15.7 0 0 0 1.4 3.6A8 8 0 0 1 5.1 16zm3-8h-3a8 8 0 0 1 4.4-3.6A15.7 15.7 0 0 0 8.1 8zM12 20a14 14 0 0 1-1.9-4h3.8A14 14 0 0 1 12 20zm2.3-6H9.7a14.7 14.7 0 0 1 0-4h4.6a14.7 14.7 0 0 1 0 4zm.2 5.6a15.7 15.7 0 0 0 1.4-3.6h3a8 8 0 0 1-4.4 3.6zm1.8-5.6a16.5 16.5 0 0 0 0-4h3.4a8 8 0 0 1 0 4z"/></svg>
        www.coastaltundrabridgeadvisory.example
      </li>
    </ul>
    <p class="address">PO Box 418259 Quillwater, Alaska 99642</p>
  </section>
</main>
</body>
</html>
```